Global (re)insurance broker needs a business card design

We need a classic business card for our company that is headquartered in SG, with offices in Malaysia and Dubai. We specialise in insurance and reinsurance broking and consultancy for our global clients.

```html
<!DOCTYPE html>
<html lang="en">
<head>
<meta charset="utf-8">
<title>Norvale Business Card</title>
<link href="https://fonts.googleapis.com/css2?family=Open+Sans:wght@400;700&display=swap" rel="stylesheet">
<style>
  :root {
    --backdrop: #2b2b2e;
    --card: #161616;
    --edge: #2b4ea0;
    --brand-blue: #2b4ea0;
    --brand-mint: #c4dcb8;
    --text-light: #f2f2f2;
    --text-muted: #d6d6d6;
  }
  * { margin: 0; padding: 0; box-sizing: border-box; }
  html, body {
    width: 1200px; height: 947px; overflow: hidden;
    background: var(--backdrop);
    font-family: "Open Sans", Arial, sans-serif;
  }
  .canvas { position: relative; width: 1200px; height: 947px; }
  .card {
    position: absolute; top: 313px;
    width: 540px; height: 320px;
    background: var(--card);
    border: 3px solid var(--edge);
    border-bottom-width: 6px;
    border-radius: 20px;
    overflow: hidden;
  }
  .card--front { left: 30px; }
  .card--back { left: 630px; }
  .wordmark {
    font-weight: 700; color: var(--brand-mint);
    letter-spacing: 2px; line-height: 1;
  }
  .card--front .wordmark {
    position: absolute; left: 0; right: 0; top: 120px;
    text-align: center; font-size: 72px;
  }
  .card--back .wordmark {
    position: absolute; left: 40px; top: 112px; font-size: 50px;
  }
  .tab {
    position: absolute; right: 22px; top: 0;
    width: 12px; height: 44px; background: var(--brand-blue);
  }
  .person {
    position: absolute; right: 44px; top: 18px; text-align: right;
  }
  .person__name { font-weight: 700; font-size: 22px; color: var(--brand-blue); }
  .person__title { font-size: 13px; color: var(--text-muted); }
  .address {
    position: absolute; right: 40px; top: 168px;
    text-align: right; font-size: 12.5px; line-height: 1.5; color: var(--text-light);
  }
  .contacts {
    position: absolute; left: 40px; bottom: 22px;
    list-style: none; font-size: 13px; line-height: 1.6; color: var(--text-light);
  }
  .contacts li { display: flex; align-items: center; gap: 8px; }
  .contacts svg { width: 12px; height: 12px; fill: var(--brand-blue); flex: none; }
</style>
</head>
<body>
<div class="canvas">
  <section class="card card--front">
    <div class="wordmark">NORVALE</div>
  </section>

  <section class="card card--back">
    <div class="tab"></div>
    <div class="person">
      <div class="person__name">Mei Lin Koh</div>
      <div class="person__title">Chief Operating Officer</div>
    </div>
    <div class="wordmark">NORVALE</div>
    <address class="address" style="font-style:normal">
      25 Harbour Lane,<br>
      Marina Tower #08-04,<br>
      Singapore 018956
    </address>
    <ul class="contacts">
      <li>
        <svg viewBox="0 0 24 24" aria-hidden="true"><path d="M6.6 10.8a15 15 0 0 0 6.6 6.6l2.2-2.2a1 1 0 0 1 1-.25 11.4 11.4 0 0 0 3.6.57 1 1 0 0 1 1 1V20a1 1 0 0 1-1 1A17 17 0 0 1 3 4a1 1 0 0 1 1-1h3.5a1 1 0 0 1 1 1c0 1.25.2 2.45.57 3.57a1 1 0 0 1-.25 1z"/></svg>
        +65 9123 4567
      </li>
      <li>
        <svg viewBox="0 0 24 24" aria-hidden="true"><path d="M2 5h20v14H2z M2 5l10 8 10-8" /></svg>
        meilin@norvale.com
      </li>
      <li>
        <svg viewBox="0 0 24 24" aria-hidden="true"><circle cx="12" cy="12" r="10"/></svg>
        www.norvale.com
      </li>
    </ul>
  </section>
</div>
</body>
</html>
```